Marlowby Services Website Design

We have most content but require a professional design. We have a logo already and will need it utilized along with several of the photos from the attached documentation.
First page should have our mission and Vision and the synapsis provided in the word document. Visitors will be prompted to select from one of our 3 divisions from this page.
Each division will have the same list of tabs : About, Services, Safety, Careers and Contact.
Photos on each divisions page should be representative of the divisions offerings. The word doc attached contains the requested content and we are open to edits that would complement and fill the website.
I like the Quorvane site www.quorvane.example - they are our competition so cant be modeled directly after this.
Please include prompts to request quote at each service page. align the format of the geotechnical page to the other 2 divisions.
I used chat gpt for some of the content so will need it optimized for SCO.

```html
<!DOCTYPE html>
<html lang="en">
<head>
<meta charset="utf-8">
<title>Marlowby Services</title>
<link rel="stylesheet" href="https://fonts.googleapis.com/css2?family=Roboto:wght@400;500;700&family=Michroma&display=swap">
<style>
:root{
  --red:#ed1c24;
  --red-deep:#d9161e;
  --ink:#111111;
  --text:#555555;
  --grey-band:#8c8c8c;
  --dark:#14171c;
  --white:#ffffff;
  --card-shadow:0 4px 18px rgba(0,0,0,.12);
}
*{box-sizing:border-box;margin:0;padding:0}
html,body{width:1200px;height:2705px;overflow:hidden;background:var(--white)}
body{font-family:"Roboto",Arial,sans-serif;color:var(--ink)}
.page{position:relative;width:1200px;height:2705px;overflow:hidden}
.abs{position:absolute}
.brand{font-family:"Roboto",Arial,sans-serif;font-weight:700;color:var(--red);letter-spacing:3px;text-transform:uppercase}

/* header */
.site-header{top:0;left:0;width:1200px;height:82px;border-top:4px solid var(--red);background:var(--white);z-index:3}
.site-header .brand{left:143px;top:22px;font-size:32px}
.main-nav{left:526px;top:34px;display:flex;gap:36px;font-size:14px;font-weight:500}
.quote-btn{left:936px;top:25px;width:119px;height:34px;background:var(--red);color:var(--white);font-size:14px;font-weight:500;display:flex;align-items:center;justify-content:center}

/* hero */
.hero-art{top:82px;left:0}
.hero-copy{left:143px;top:250px;color:var(--white)}
.hero-copy .brand{font-size:44px;letter-spacing:4px}
.hero-copy p{margin-top:18px;width:480px;font-size:16px;line-height:26px;font-weight:500}
.btn{display:inline-flex;align-items:center;justify-content:center;gap:8px;font-weight:700;text-transform:uppercase}
.btn-red{background:var(--red);color:var(--white)}
.hero-copy .btn{margin-top:24px;width:162px;height:47px;font-size:15px}

/* divisions */
.division{top:816px;width:284px;height:222px;background:var(--white);box-shadow:var(--card-shadow);text-align:center}
.division .badge{width:88px;height:88px;border-radius:50%;background:var(--red);margin:50px auto 0;display:flex;align-items:center;justify-content:center}
.division h3{margin-top:18px;font-size:18px;font-weight:700}

/* mission & vision */
.mv-art{top:1118px;left:0}
.mv-block{top:1190px;color:var(--white)}
.mv-head{display:flex;align-items:center;gap:24px}
.mv-icon{width:76px;height:76px;border-radius:50%;background:var(--white);display:flex;align-items:center;justify-content:center}
.mv-head h2{font-size:20px;font-weight:700}
.mv-block p{margin-top:22px;width:383px;font-size:14px;line-height:23px;text-align:justify}
.btn-light{position:absolute;top:220px;width:161px;height:40px;background:var(--white);font-size:13px}

/* services */
.section-title{top:1572px;left:0;width:1200px;text-align:center;font-family:"Michroma",sans-serif;font-size:38px;letter-spacing:1px;color:var(--ink)}
.section-title span{color:var(--red)}
.service{width:288px;height:413px;background:var(--white);border-radius:10px;box-shadow:var(--card-shadow);text-align:center}
.service .photo{display:block;margin:7px 7px 0;width:274px;height:200px;border-radius:8px}
.service h3{margin-top:28px;font-size:18px;font-weight:700}
.service p{margin:12px auto 0;width:262px;font-size:13px;line-height:23px;color:var(--text)}
.service .btn{margin-top:19px;width:148px;height:39px;font-size:14px}
.arrow{top:1845px}

/* footer */
.footer-art{top:2117px;left:0}
.footer-title{color:var(--white);font-size:22px;font-weight:700}
.field{left:143px;width:253px;height:41px;background:var(--white);border-radius:2px;font-size:13px;color:#666;padding:0 17px;display:flex;align-items:center}
.submit{left:143px;top:2593px;width:253px;height:41px;font-size:14px;border-radius:2px}
.vline{top:2395px;height:245px;border-left:1px dashed #4a4e55}
.hline{left:487px;width:258px;border-top:1px dashed #4a4e55}
.detail{left:483px;display:flex;gap:12px;color:var(--white)}
.detail .ring{width:39px;height:39px;border-radius:50%;border:1.5px solid var(--white);display:flex;align-items:center;justify-content:center;flex:none;margin-top:4px}
.detail h4{font-size:14px;font-weight:700}
.detail span{display:block;margin-top:9px;font-size:13px}
.footer-brand{left:813px;top:2440px;font-size:30px}
.socials{left:858px;top:2496px;display:flex;gap:11px}
.socials i{width:40px;height:40px;border-radius:50%;border:1.5px solid var(--white);display:block}
.copyright{left:838px;top:2558px;color:var(--white);font-size:13px}
</style>
</head>
<body>
<div class="page">

  <header class="site-header abs">
    <div class="brand abs">Marlowby</div>
    <nav class="main-nav abs"><span>HOME</span><span>ABOUT US</span><span>SERVICES</span><span>CAREERS</span></nav>
    <div class="quote-btn abs">Get A Quote</div>
  </header>

  <svg class="hero-art abs" width="1200" height="700" viewBox="0 82 1200 700">
    <defs>
      <linearGradient id="heroTone" x1="0" y1="0" x2="1" y2="1">
        <stop offset="0" stop-color="#4d5a45"/>
        <stop offset=".5" stop-color="#6d6f69"/>
        <stop offset="1" stop-color="#4a5047"/>
      </linearGradient>
    </defs>
    <polygon role="img" aria-label="Aerial photo of a boom lift raised above a small town neighbourhood" fill="url(#heroTone)" points="0,82 1200,82 1200,610 615,660 0,712"/>
    <polygon fill="var(--red)" points="615,660 1200,610 1200,780"/>
  </svg>

  <div class="hero-copy abs">
    <div class="brand">Marlowby</div>
    <p>Marlowby is a full-service wind energy service provider specializing in blade access and repair, service and maintenance.</p>
    <div class="btn btn-red">Get Started
      <svg width="14" height="14" viewBox="0 0 14 14"><circle cx="7" cy="7" r="7" fill="#fff"/><path d="M5.5 4l3 3-3 3" stroke="var(--red)" stroke-width="2" fill="none"/></svg>
    </div>
  </div>

  <div class="division abs" style="left:144px">
    <div class="badge"><svg width="50" height="50" viewBox="0 0 50 50" fill="none" stroke="#fff" stroke-width="2"><path d="M25 5l16 6v12c0 10-7 17-16 21C16 40 9 33 9 23V11z"/><rect x="18" y="22" width="12" height="10" rx="1"/><path d="M20 22v-4a4 4 0 018 0v4"/><circle cx="34" cy="34" r="9" fill="var(--red)"/><circle cx="34" cy="31" r="3"/><path d="M28 40c2-4 10-4 12 0"/></svg></div>
    <h3>Aerial Access</h3>
  </div>
  <div class="division abs" style="left:457px">
    <div class="badge"><svg width="50" height="50" viewBox="0 0 50 50" fill="none" stroke="#fff" stroke-width="2"><circle cx="17" cy="15" r="6"/><circle cx="17" cy="15" r="10" stroke-dasharray="4 3"/><rect x="28" y="6" width="10" height="20"/><path d="M33 26v8l-2 3 4 3-2 3 1 4"/></svg></div>
    <h3>Geotechnical Drilling</h3>
  </div>
  <div class="division abs" style="left:770px">
    <div class="badge"><svg width="50" height="50" viewBox="0 0 50 50" fill="none" stroke="#fff" stroke-width="2"><circle cx="25" cy="18" r="11" stroke-dasharray="3 3"/><path d="M27 10l-5 9h6l-4 8"/><path d="M6 24l4 12 7 6v4M44 24l-4 12-7 6v4M12 28l6 8M38 28l-6 8"/></svg></div>
    <h3>Renewable Energy Services</h3>
  </div>

  <svg class="mv-art abs" width="1200" height="402" viewBox="0 1118 1200 402">
    <defs>
      <linearGradient id="redTone" x1="0" y1="0" x2="1" y2="1"><stop offset="0" stop-color="#e4262d"/><stop offset="1" stop-color="#ec1f27"/></linearGradient>
      <linearGradient id="greyTone" x1="0" y1="0" x2="1" y2="1"><stop offset="0" stop-color="#8e8e8e"/><stop offset="1" stop-color="#7d7d7d"/></linearGradient>
    </defs>
    <polygon role="img" aria-label="Red tinted aerial photo of the lift over town" fill="url(#redTone)" points="0,1118 600,1172 600,1468 0,1520"/>
    <polygon role="img" aria-label="Grey tinted aerial photo of the lift over town" fill="url(#greyTone)" points="600,1172 1200,1118 1200,1520 600,1468"/>
  </svg>

  <div class="mv-block abs" style="left:143px">
    <div class="mv-head">
      <div class="mv-icon"><svg width="42" height="42" viewBox="0 0 42 42" fill="none" stroke="var(--red)" stroke-width="1.8"><path d="M20 6v16M20 6h10l-3 4 3 4H20"/><path d="M4 30l8-4h10a2 2 0 010 4h-7M22 30l10-5a2 2 0 012 3L22 36H8"/></svg></div>
      <h2>MISSION</h2>
    </div>
    <p>At Marlowby, our mission is to deliver unparalleled aerial access, geotechnical drilling, and service and maintenance solutions, consistently exceeding our clients' expectations. We strive to achieve this by investing in cutting-edge technology.</p>
    <div class="btn btn-light" style="left:0;color:var(--red)">Learn More
      <svg width="12" height="12" viewBox="0 0 14 14"><circle cx="7" cy="7" r="7" fill="var(--red)"/><path d="M5.5 4l3 3-3 3" stroke="#fff" stroke-width="2" fill="none"/></svg></div>
  </div>

  <div class="mv-block abs" style="left:672px">
    <div class="mv-head">
      <div class="mv-icon"><svg width="44" height="44" viewBox="0 0 44 44" fill="none" stroke="#888" stroke-width="1.8"><circle cx="22" cy="22" r="14" stroke-dasharray="4 3"/><path d="M8 22c5-7 23-7 28 0-5 7-23 7-28 0z"/><circle cx="22" cy="22" r="4"/></svg></div>
      <h2>VISION</h2>
    </div>
    <p>To be the leading provider of aerial access, geotechnical drilling, and service solutions, setting the standard for excellence in safety, efficiency, and environmental stewardship.</p>
    <div class="btn btn-light" style="left:1px;color:#888">Learn More
      <svg width="12" height="12" viewBox="0 0 14 14"><circle cx="7" cy="7" r="7" fill="#888"/><path d="M5.5 4l3 3-3 3" stroke="#fff" stroke-width="2" fill="none"/></svg></div>
  </div>

  <h2 class="section-title abs"><span>OUR</span> SERVICES</h2>

  <svg class="arrow abs" style="left:80px" width="22" height="36" viewBox="0 0 22 36"><path d="M18 3L4 18l14 15" stroke="#999" stroke-width="3" fill="none"/></svg>
  <svg class="arrow abs" style="left:1099px" width="22" height="36" viewBox="0 0 22 36"><path d="M4 3l14 15L4 33" stroke="#999" stroke-width="3" fill="none"/></svg>

  <article class="service abs" style="left:146px;top:1657px">
    <svg class="photo" role="img" aria-label="Photo of a courier holding a parcel beside a van" viewBox="0 0 274 200"><defs><linearGradient id="p1" x1="0" y1="0" x2="1" y2="1"><stop offset="0" stop-color="#cfd3d6"/><stop offset="1" stop-color="#8a7c66"/></linearGradient></defs><rect width="274" height="200" fill="url(#p1)"/></svg>
    <h3>Delivering safe</h3>
    <p>Lorem ipsum dolor sit amet, consectetur adipiscing elit, sed do eiusmod tempor labore et dolore magna aliqua.</p>
    <div class="btn btn-red">Learn More <svg width="12" height="12" viewBox="0 0 14 14"><circle cx="7" cy="7" r="7" fill="#fff"/><path d="M5.5 4l3 3-3 3" stroke="var(--red)" stroke-width="2" fill="none"/></svg></div>
  </article>

  <article class="service abs" style="left:458px;top:1681px">
    <svg class="photo" role="img" aria-label="Photo of two engineers in hard hats reviewing plans near wind turbines" viewBox="0 0 274 200"><defs><linearGradient id="p2" x1="0" y1="0" x2="0" y2="1"><stop offset="0" stop-color="#4f93d3"/><stop offset=".7" stop-color="#a7c9e6"/><stop offset="1" stop-color="#b7a27a"/></linearGradient></defs><rect width="274" height="200" fill="url(#p2)"/></svg>
    <h3>Construction</h3>
    <p>Lorem ipsum dolor sit amet, consectetur adipiscing elit, sed do eiusmod tempor labore et dolore magna aliqua.</p>
    <div class="btn btn-red">Learn More <svg width="12" height="12" viewBox="0 0 14 14"><circle cx="7" cy="7" r="7" fill="#fff"/><path d="M5.5 4l3 3-3 3" stroke="var(--red)" stroke-width="2" fill="none"/></svg></div>
  </article>

  <article class="service abs" style="left:770px;top:1657px">
    <svg class="photo" role="img" aria-label="Photo of a technician seated on top of a wind turbine above green hills" viewBox="0 0 274 200"><defs><linearGradient id="p3" x1="0" y1="0" x2="0" y2="1"><stop offset="0" stop-color="#7f95a8"/><stop offset=".55" stop-color="#8c9a76"/><stop offset="1" stop-color="#d8dde0"/></linearGradient></defs><rect width="274" height="200" fill="url(#p3)"/></svg>
    <h3>Renewable energy industries</h3>
    <p>Lorem ipsum dolor sit amet, consectetur adipiscing elit, sed do eiusmod tempor labore et dolore magna aliqua.</p>
    <div class="btn btn-red">Learn More <svg width="12" height="12" viewBox="0 0 14 14"><circle cx="7" cy="7" r="7" fill="#fff"/><path d="M5.5 4l3 3-3 3" stroke="var(--red)" stroke-width="2" fill="none"/></svg></div>
  </article>

  <svg class="footer-art abs" width="1200" height="588" viewBox="0 2117 1200 588">
    <polygon fill="var(--red)" points="0,2117 590,2237 0,2287"/>
    <polygon fill="var(--dark)" points="0,2287 590,2237 1200,2185 1200,2705 0,2705"/>
  </svg>

  <h3 class="footer-title abs" style="left:143px;top:2342px">CONTACT</h3>
  <div class="field abs" style="top:2394px">Name</div>
  <div class="field abs" style="top:2444px">Email</div>
  <div class="field abs" style="top:2493px">Phone</div>
  <div class="field abs" style="top:2543px">Message</div>
  <div class="btn btn-red submit abs">Submit Now</div>

  <div class="vline abs" style="left:440px"></div>
  <div class="vline abs" style="left:785px"></div>

  <h3 class="footer-title abs" style="left:487px;top:2344px">CONTACT DETAILS</h3>
  <div class="detail abs" style="top:2412px">
    <div class="ring"><svg width="14" height="18" viewBox="0 0 14 18"><path d="M7 1a6 6 0 016 6c0 4-6 10-6 10S1 11 1 7a6 6 0 016-6z" fill="#fff"/><circle cx="7" cy="7" r="2.2" fill="var(--dark)"/></svg></div>
    <div><h4>Address</h4><span>218 Larch Ave. Ashgrove Fields, AB T0X-4B1</span></div>
  </div>
  <div class="hline abs" style="top:2483px"></div>
  <div class="detail abs" style="top:2500px">
    <div class="ring"><svg width="16" height="16" viewBox="0 0 16 16"><path d="M3 1l3 3-1.5 2a9 9 0 005 5L11.5 9.5l3 3L13 15C7 15 1 9 1 3z" fill="#fff"/></svg></div>
    <div><h4>Phone</h4><span>(555) 014-2290</span></div>
  </div>
  <div class="hline abs" style="top:2566px"></div>
  <div class="detail abs" style="top:2583px">
    <div class="ring"><svg width="17" height="13" viewBox="0 0 17 13"><rect width="17" height="13" rx="2" fill="#fff"/><path d="M1 2l7.5 5.5L16 2" stroke="var(--dark)" stroke-width="1.5" fill="none"/></svg></div>
    <div><h4>Email Address</h4><span>info@marlowbyservices.example</span></div>
  </div>

  <div class="brand footer-brand abs">Marlowby</div>
  <div class="socials abs" aria-label="Social media links"><i></i><i></i><i></i></div>
  <div class="copyright abs">2024 by Marlowby Services Inc.</div>

</div>
</body>
</html>
```